Employee Benefits and Insurance Consulting

We are an existing company with over 30 years experience but are changing our name. We would like a simple design with grey tones.

Industry/Entity Type

Insurance

Contact Information for Business Card

Marlow Benefits Consulting
Gerald P Hollins CEO
5172 Brackenridge Road
Alder Falls, OR 97999
gerald@marlowbenefits-example.com
555-412-5593 - O
555-247-3861 - C

```html
<!DOCTYPE html>
<html lang="en">
<head>
<meta charset="utf-8">
<title>Marlow Benefits Consulting – Business Card</title>
<link rel="stylesheet" href="https://fonts.googleapis.com/css2?family=Open+Sans:wght@400;600;700&display=swap">
<style>
  :root {
    --brand-red: #d51317;
    --brand-black: #1e1e1e;
    --ink: #1a1a1a;
    --paper: #ffffff;
    --stage: #e6e4e2;
  }
  * { box-sizing: border-box; margin: 0; padding: 0; }
  html, body {
    width: 1200px; height: 900px; overflow: hidden;
    background: var(--stage);
    font-family: "Open Sans", Arial, sans-serif;
  }
  .canvas { position: relative; width: 1200px; height: 900px; }
  .card {
    position: absolute; background: var(--paper); overflow: hidden;
    box-shadow: 0 4px 14px rgba(0,0,0,0.18);
  }
  .card svg.shapes { position: absolute; inset: 0; }

  /* Front */
  .card--front { left: 77px; top: 34px; width: 589px; height: 362px; }
  .company-name {
    position: absolute; left: 28px; top: 64px;
    font-size: 27px; font-weight: 700; color: var(--brand-black);
    letter-spacing: -0.2px; white-space: nowrap;
  }
  .person { position: absolute; right: 36px; top: 140px; text-align: right; color: var(--paper); }
  .person__name { font-size: 21px; font-weight: 700; line-height: 28px; }
  .person__title { font-size: 13px; font-weight: 600; line-height: 16px; }
  .contact-list { position: absolute; left: 28px; top: 212px; list-style: none; }
  .contact-list li {
    display: flex; align-items: center; gap: 12px;
    font-size: 15px; color: var(--ink); height: 24.5px;
  }
  .contact-list svg { width: 12px; height: 12px; fill: var(--brand-red); flex: none; }
  .address {
    position: absolute; left: 30px; top: 312px;
    font-size: 15px; line-height: 22px; color: var(--paper); font-style: normal;
    white-space: nowrap;
  }

  /* Back */
  .card--back { left: 388px; top: 505px; width: 566px; height: 352px; }
  .back-name {
    position: absolute; left: 0; right: 0; top: 186px; text-align: center;
    font-size: 30px; font-weight: 700; color: var(--brand-red); white-space: nowrap;
  }
  .back-email {
    position: absolute; right: 12px; top: 310px;
    font-size: 14px; font-weight: 600; color: var(--ink);
  }
</style>
</head>
<body>
<main class="canvas">

  <section class="card card--front" aria-label="Business card front">
    <svg class="shapes" width="589" height="362" viewBox="0 0 589 362" aria-hidden="true">
      <rect x="0" y="173" width="589" height="14" fill="var(--brand-red)"/>
      <polygon points="370,137 589,137 589,187 347,187" fill="var(--brand-red)"/>
      <polygon points="0,309 222,309 250,343 0,343" fill="var(--brand-black)"/>
      <rect x="0" y="343" width="589" height="16" fill="var(--brand-black)"/>
    </svg>
    <div class="company-name">Marlow Benefits Consulting</div>
    <div class="person">
      <div class="person__name">Gerald P Hollins</div>
      <div class="person__title">CEO</div>
    </div>
    <ul class="contact-list">
      <li>
        <svg viewBox="0 0 24 24" aria-label="Office phone"><path d="M6.6 10.8a15.1 15.1 0 0 0 6.6 6.6l2.2-2.2c.3-.3.7-.4 1-.2 1.1.4 2.3.6 3.6.6.6 0 1 .4 1 1V20c0 .6-.4 1-1 1C10.6 21 3 13.4 3 4c0-.6.4-1 1-1h3.5c.6 0 1 .4 1 1 0 1.3.2 2.5.6 3.6.1.3 0 .7-.2 1z"/></svg>
        <span>555-247-3861</span>
      </li>
      <li>
        <svg viewBox="0 0 24 24" aria-label="Mobile phone"><path d="M7 1h10a2 2 0 0 1 2 2v18a2 2 0 0 1-2 2H7a2 2 0 0 1-2-2V3a2 2 0 0 1 2-2zm0 3v14h10V4z"/></svg>
        <span>555-412-5593</span>
      </li>
      <li>
        <svg viewBox="0 0 24 24" aria-label="Email"><path d="M2 5h20v14H2zm2 2v.5l8 5 8-5V7l-8 5z"/></svg>
        <span>gerald@marlowbenefits-example.com</span>
      </li>
    </ul>
    <address class="address">
      5172 Brackenridge Road<br>Alder Falls, OR 97999
    </address>
  </section>

  <section class="card card--back" aria-label="Business card back">
    <svg class="shapes" width="566" height="352" viewBox="0 0 566 352" aria-hidden="true">
      <rect x="0" y="0" width="566" height="14" fill="var(--brand-red)"/>
      <polygon points="0,282 374,282 354,313 0,313" fill="var(--brand-red)"/>
      <polygon points="390,282 566,282 566,305 380,305" fill="var(--brand-black)"/>
      <rect x="0" y="338" width="566" height="14" fill="var(--brand-black)"/>
    </svg>
    <div class="back-name">Marlow Benefits Consulting</div>
    <div class="back-email">gerald@marlowbenefits-example.com</div>
  </section>

</main>
</body>
</html>
```